Flyer, poster, banner and social media titles designs for Community Mending Chartre

The Harbourline Charter for Community Mending provide a nationally agreed framework to guide recovery policy and practice across Australia. The Principles support recovery practitioners, governments, non-government organisations and communities to deliver effective, community-centred recovery outcomes.
The Principles have recently been refreshed through extensive consultation and we require a contemporary visual identity and design suite that will increase awareness, engagement and practical application of the Principles.
The redesign will cover:
• A4 Brochure (primary publication)
• A3 Poster
• Pull up banner
• Social Media Tiles
The new design should:
• Create a recognisable brand for the Harbourline Charter.
• Appeal to both experienced and emerging recovery practitioners.
• Reflect contemporary disaster recovery practice.
• Feel people-focused rather than government-focused.
• Support future resources such as videos, implementation guides, presentations and workshop materials.
• Remain relevant for several years without requiring a major redesign.
Target Audience
• Disaster recovery practitioners
• Government agencies
• Non-government organisations
• Community recovery workers
• Recovery managers and leaders
• Community stakeholders and volunteers
The visual identity should reflect the six Principles:
• Understanding Context
• Recognising Complexity
• Community-Centred Approaches
• Coordination
• Communication
• Capacity Building
The design should communicate:
• Recovery is centred on people and communities.
• Recovery is collaborative and involves many sectors.
• Recovery is adaptive, inclusive and evidence-informed.
• Recovery supports resilience and long-term wellbeing.
• The Principles provide practical guidance for recovery practice.
We are looking for:
• Modern and professional
• Warm and approachable
• Human-centred
• Inclusive and accessible
• Australian in context
• Visually engaging
• Suitable for print and digital use
We would like to avoid:
• Images of disaster destruction
• Emergency response imagery (fire trucks, flashing lights, etc.)
• Overly corporate or bureaucratic designs
• Designs that focus on deficits rather than recovery and growth
Consider themes such as:
• Connection and collaboration
• Communities and people
• Growth, recovery and renewal
Accessibility
Designs should:
• Meet accessibility best practice
• Use clear typography
• Achieve strong colour contrast
• Be suitable for both digital and print formats

Deliverables
1. Principles Brochure
• A4 trifold size x 2 (online and print friendly version)
• A side to include cover side, logos side and overview of principles.
• B side full details of the principles
• Graphic to highlight the 3 c’s concept (RECOVERY Context, complexity, community centred, coordinate, communicate and capacity). Currently 3 circles.
• Can be printed and distributed electronically
2. Poster
• A1 and A3 versions
• Suitable for office and workshop display
3. Pull-Up Banner - 850 mm (W) × 2000 mm (H)
• Conference and event use
• High visual impact
• Strong branding and concise messaging
4. Social Media Tiles x 3

We are providing an extension and increasing the budget following feedback from designers. We are wanting the resources to look and feel different from the existing designs, considering either a different colour palette in the designs or different motif with the leave design. Any nature based designs should consider the Australian fauna or flora. Also suggest avoiding images in the designs. The principles are not numbered or liner in the concept of how they function. Happy to answer any further questions and thank you for your suggested concepts.

Disaster recovery practitioners, Government agencies , Non-government organisations, Community recovery workers and Community stakeholders and volunteers

Disaster recovery

• Modern, warm, visually engaging, human-centred, Australian in context and different to the current design.
• Symbols for each principles
• Images of disaster destruction, Emergency response imagery, Overly corporate or bureaucratic designs, Designs that focus on deficits rather than recovery and growth, avoid too much black

```html
<!DOCTYPE html>
<html lang="en">
<head>
<meta charset="utf-8">
<title>Harbourline Charter for Community Mending – Trifold Brochure</title>
<link href="https://fonts.googleapis.com/css2?family=Poppins:wght@400;600;700;800&family=Open+Sans:wght@400;600&display=swap" rel="stylesheet">
<style>
  :root{
    --backdrop:#b7d5b0;
    --teal-deep:#1c4d5c;
    --teal:#2c6877;
    --green:#5c9b4a;
    --green-light:#8fc07a;
    --wattle:#e9a93a;
    --orange:#e5782c;
    --ink:#2b3236;
    --muted:#545d61;
    --paper:#ffffff;
    --mist:#f1f4f1;
  }
  *{box-sizing:border-box;margin:0;padding:0}
  html,body{width:1200px;height:900px;overflow:hidden}
  body{background:var(--backdrop);font-family:"Open Sans",Arial,sans-serif;color:var(--ink);position:relative}

  .trifold{position:absolute;top:248px;width:570px;height:403px;display:flex;background:var(--paper);box-shadow:0 8px 24px rgba(30,60,40,.25);overflow:hidden}
  .trifold--outside{left:20px}
  .trifold--inside{left:610px}
  .panel{position:relative;width:190px;height:403px;overflow:hidden}
  .panel + .panel{border-left:1px solid rgba(0,0,0,.06)}

  /* outside: intro */
  .intro{padding:18px 14px 0}
  .intro__title{font-family:"Poppins",sans-serif;font-weight:700;font-size:11px;line-height:1.2;color:var(--teal-deep);margin-bottom:7px}
  .intro p{font-size:5.6px;line-height:1.5;color:var(--muted);margin-bottom:5px}
  .intro__lead{font-family:"Poppins",sans-serif;font-weight:700;font-size:7px;color:var(--green);margin-top:6px}
  .intro__ground{position:absolute;left:0;bottom:0;width:190px;height:90px}

  /* outside: partners */
  .partners{background:linear-gradient(160deg,var(--mist) 0%,#e4e9e5 100%)}
  .partner-badge{position:absolute;width:30px;height:30px;border-radius:50%;background:var(--paper);box-shadow:0 1px 3px rgba(0,0,0,.14)}
  .partners__label{position:absolute;left:20px;top:212px;width:120px;font-family:"Poppins",sans-serif;font-weight:700;font-size:7px;line-height:1.25;color:var(--teal-deep);text-align:center}

  /* mending cluster straddling intro and partner panels */
  .cluster{position:absolute;left:118px;top:256px;width:136px;height:136px}

  /* outside: cover */
  .cover__art{position:absolute;inset:0}
  .cover__title{position:absolute;left:14px;right:10px;bottom:24px;font-family:"Poppins",sans-serif;color:var(--paper)}
  .cover__kicker{font-weight:700;font-size:8px;margin-bottom:3px}
  .cover__main{font-weight:800;font-size:24px;line-height:1.05}
  .cover__accent{font-weight:800;font-size:24px;line-height:1.05;color:var(--green-light)}

  /* inside */
  .inside-bg{position:absolute;inset:0}
  .principle-panel{position:relative;padding:0 12px}
  .principle{position:relative;margin-bottom:8px}
  .principle__icon{width:20px;height:20px;border-radius:50%;background:var(--paper);border:1.5px solid var(--green-light);display:flex;align-items:center;justify-content:center;margin-bottom:4px}
  .principle__title{font-family:"Poppins",sans-serif;font-weight:700;font-size:7px;line-height:1.15;color:var(--ink);margin-bottom:3px}
  .principle__title strong{text-transform:uppercase;font-weight:800}
  .principle ul{list-style:none}
  .principle li{position:relative;padding-left:6px;font-size:5.3px;line-height:1.42;color:var(--muted);margin-bottom:1.5px}
  .principle li::before{content:"";position:absolute;left:0;top:2.6px;width:2.6px;height:2.6px;border-radius:50%;background:var(--orange)}
</style>
</head>
<body>

<section class="trifold trifold--outside" aria-label="Brochure outside: introduction, partners and cover">
  <div class="panel intro">
    <h2 class="intro__title">Harbourline Charter for<br>Community Mending</h2>
    <p>Disasters can deeply impact lives and livelihoods. Working with communities as they mend is complex and challenging. Mending is long-term, multi-layered and dynamic, and these principles guide our planning, our efforts and our decision-making.</p>
    <p>Community mending is part of emergency management, which includes prevention, preparedness and response. Planning for mending is integral to preparation and mitigation actions.</p>
    <p>Mending includes built, environmental, social and economic elements, as well as individual and community wellbeing, offering a chance to build stronger communities.</p>
    <p>The principles work together rather than in order. Each one informs the others, and all remain equally critical.</p>
    <p class="intro__lead">Successful Mending</p>
    <svg class="intro__ground" viewBox="0 0 190 90" aria-hidden="true">
      <path d="M0,50 C50,32 110,70 190,50 L190,90 L0,90 Z" fill="#8fc07a"/>
      <path d="M0,62 C60,48 120,82 190,64 L190,90 L0,90 Z" fill="#5c9b4a"/>
    </svg>
  </div>

  <div class="panel partners" aria-label="Development partner badges">
    <span class="partner-badge" style="left:40px;top:40px"></span>
    <span class="partner-badge" style="left:80px;top:58px"></span>
    <span class="partner-badge" style="left:118px;top:76px"></span>
    <span class="partner-badge" style="left:150px;top:96px"></span>
    <span class="partner-badge" style="left:20px;top:80px"></span>
    <span class="partner-badge" style="left:60px;top:98px"></span>
    <span class="partner-badge" style="left:100px;top:116px"></span>
    <span class="partner-badge" style="left:138px;top:138px"></span>
    <span class="partner-badge" style="left:16px;top:124px"></span>
    <span class="partner-badge" style="left:54px;top:142px"></span>
    <span class="partner-badge" style="left:96px;top:162px"></span>
    <span class="partner-badge" style="left:24px;top:172px"></span>
    <p class="partners__label">Partners In<br>Development From The</p>
  </div>

  <div class="panel cover">
    <svg class="cover__art" viewBox="0 0 190 403" aria-hidden="true">
      <rect width="190" height="403" fill="#f6f8f6"/>
      <path d="M120,0 C200,60 200,240 60,262 C30,267 10,270 0,272 L0,403 L190,403 L190,0 Z" fill="#5c9b4a"/>
      <path d="M142,0 C212,70 200,250 70,275 C40,281 15,285 0,288 L0,403 L190,403 L190,0 Z" fill="#1c4d5c"/>
      <circle cx="96" cy="150" r="62" fill="#1c4d5c"/>
      <circle cx="96" cy="150" r="56" fill="#ffffff"/>
      <g stroke="#c9d8cc" stroke-width="1">
        <line x1="96" y1="150" x2="96" y2="116"/><line x1="96" y1="150" x2="125" y2="133"/>
        <line x1="96" y1="150" x2="125" y2="167"/><line x1="96" y1="150" x2="96" y2="184"/>
        <line x1="96" y1="150" x2="67" y2="167"/><line x1="96" y1="150" x2="67" y2="133"/>
      </g>
      <circle cx="96" cy="150" r="12" fill="#e9a93a"/>
      <circle cx="96" cy="116" r="9" fill="#5c9b4a"/>
      <circle cx="125" cy="133" r="9" fill="#7b62b0"/>
      <circle cx="125" cy="167" r="9" fill="#e5782c"/>
      <circle cx="96" cy="184" r="9" fill="#2c6877"/>
      <circle cx="67" cy="167" r="9" fill="#3b8fd0"/>
      <circle cx="67" cy="133" r="9" fill="#8fc07a"/>
    </svg>
    <div class="cover__title">
      <p class="cover__kicker">Harbourline Charter for</p>
      <p class="cover__main">Community</p>
      <p class="cover__accent">Mending</p>
    </div>
  </div>

  <svg class="cluster" viewBox="0 0 136 136" role="img" aria-label="Six connected principles surrounding community mending, with no set order">
    <circle cx="68" cy="68" r="67" fill="#1c4d5c"/>
    <circle cx="68" cy="68" r="62" fill="#ffffff"/>
    <g fill-opacity=".9">
      <circle cx="68" cy="31" r="21" fill="#e4f1de"/>
      <circle cx="100" cy="49.5" r="21" fill="#ebe5f5"/>
      <circle cx="100" cy="86.5" r="21" fill="#fce9d9"/>
      <circle cx="68" cy="105" r="21" fill="#e1edf1"/>
      <circle cx="36" cy="86.5" r="21" fill="#e2eef8"/>
      <circle cx="36" cy="49.5" r="21" fill="#eef5e6"/>
    </g>
    <circle cx="68" cy="68" r="18" fill="#fbf3df" stroke="#e9a93a" stroke-width="1.2"/>
    <text x="68" y="70" text-anchor="middle" font-family="Poppins, sans-serif" font-weight="700" font-size="6.2" fill="#1c4d5c">MENDING</text>
    <g font-family="Poppins, sans-serif" font-weight="600" font-size="4.8" fill="#2b3236" text-anchor="middle">
      <text x="68" y="26">Context</text>
      <text x="104" y="45">Complexity</text>
      <text x="104" y="94">Community</text>
      <text x="68" y="113">Coordinate</text>
      <text x="32" y="94">Communicate</text>
      <text x="32" y="45">Capacity</text>
    </g>
  </svg>
</section>

<section class="trifold trifold--inside" aria-label="Brochure inside: the six principles in detail">
  <svg class="inside-bg" viewBox="0 0 570 403" preserveAspectRatio="none" aria-hidden="true">
    <rect width="570" height="403" fill="#ffffff"/>
    <rect x="190" width="190" height="403" fill="#f6f7f6"/>
    <rect x="380" width="190" height="403" fill="#eceeed"/>
    <path d="M0,0 L570,0 L570,78 C500,90 460,60 380,72 C320,80 250,52 190,62 C120,72 60,44 0,52 Z" fill="#1c4d5c"/>
    <path d="M0,370 C30,355 60,385 95,368 C130,352 160,382 190,370 C225,355 255,385 285,368 C320,352 350,382 380,370 C415,355 445,385 475,368 C510,352 540,382 570,370 L570,403 L0,403 Z" fill="#5c9b4a"/>
    <path d="M0,382 C40,372 70,395 110,384 C150,374 170,394 190,386 C230,372 260,395 300,384 C340,374 360,394 380,386 C420,372 450,395 490,384 C530,374 550,394 570,386 L570,403 L0,403 Z" fill="#8fc07a"/>
  </svg>

  <div class="panel principle-panel" style="padding-top:40px">
    <div class="principle">
      <div class="principle__icon"><svg width="11" height="11" viewBox="0 0 12 12"><path d="M2,10 C2,5 6,2 10,2 C10,7 7,10 2,10 Z" fill="none" stroke="#5c9b4a" stroke-width="1.2"/></svg></div>
      <h3 class="principle__title">Understand the <strong>context</strong></h3>
      <ul>
        <li>Acknowledge existing strengths and capacity, including past experiences and future aspirations;</li>
        <li>Appreciate the risks and stressors faced by the community;</li>
        <li>Embed accessibility, equity, inclusion and diversity in practice, using culturally safe approaches;</li>
        <li>Support people who may be at greater risk or disproportionately impacted;</li>
        <li>Respect connections to Country, places and environment in every stage of mending.</li>
      </ul>
    </div>
    <div class="principle">
      <div class="principle__icon" style="border-color:#a993d0"><svg width="11" height="11" viewBox="0 0 12 12"><g fill="none" stroke="#7b62b0" stroke-width="1"><circle cx="6" cy="6" r="1.6"/><path d="M6,1 V4.4 M6,7.6 V11 M1,6 H4.4 M7.6,6 H11"/></g></svg></div>
      <h3 class="principle__title">Recognise <strong>complexity</strong></h3>
      <ul>
        <li>Acknowledge effects may extend beyond the boundaries where the event occurred;</li>
        <li>Understand needs can be limited at first and change over time;</li>
        <li>Respond with flexible action as community needs evolve rapidly;</li>
        <li>Accept that mending is not linear and setbacks can occur;</li>
        <li>Over time, support communities to cultivate hope and collective growth.</li>
      </ul>
    </div>
  </div>

  <div class="panel principle-panel" style="padding-top:56px">
    <div class="principle">
      <div class="principle__icon" style="border-color:#f0a66b"><svg width="11" height="11" viewBox="0 0 12 12"><path d="M6,10 C2,7 1,5 2.5,3 C4,1.6 5.5,2.6 6,3.8 C6.5,2.6 8,1.6 9.5,3 C11,5 10,7 6,10 Z" fill="none" stroke="#e5782c" stroke-width="1.1"/></svg></div>
      <h3 class="principle__title">Use <strong>community centred</strong> approaches:</h3>
      <ul>
        <li>Assist and enable individuals, families and the community to take part in their own mending;</li>
        <li>Recognise that people may need different support at various times;</li>
        <li>Be guided by the community's priorities;</li>
        <li>Channel effort through existing local networks and leadership;</li>
        <li>Build partnerships that reflect diverse representation.</li>
      </ul>
    </div>
    <div class="principle">
      <div class="principle__icon" style="border-color:#6fa2ad"><svg width="11" height="11" viewBox="0 0 12 12"><g fill="none" stroke="#2c6877" stroke-width="1"><circle cx="6" cy="3" r="1.5"/><circle cx="2.5" cy="9" r="1.5"/><circle cx="9.5" cy="9" r="1.5"/><path d="M5,4.3 L3.3,7.7 M7,4.3 L8.7,7.7 M4,9 H8"/></g></svg></div>
      <h3 class="principle__title"><strong>Coordinate</strong> all activities:</h3>
      <ul>
        <li>Have clearly articulated, shared goals based on desired outcomes;</li>
        <li>Be flexible, accounting for changes in community needs;</li>
        <li>Be guided by those with local experience and expertise;</li>
        <li>Reflect well-developed planning before, during and after an event;</li>
        <li>Be inclusive, building on relationships created over time.</li>
      </ul>
    </div>
  </div>

  <div class="panel principle-panel" style="padding-top:64px">
    <div class="principle">
      <div class="principle__icon" style="border-color:#7bb3de"><svg width="11" height="11" viewBox="0 0 12 12"><path d="M2,2.5 H10 V7.5 H5 L3,9.8 V7.5 H2 Z" fill="none" stroke="#3b8fd0" stroke-width="1.1"/></svg></div>
      <h3 class="principle__title"><strong>Communicate</strong> effectively:</h3>
      <ul>
        <li>Recognise that communication should be two-way, building trust through shared understanding;</li>
        <li>Ensure information is accessible to audiences in diverse situations;</li>
        <li>Establish mechanisms for coordinated, consistent messages;</li>
        <li>Ensure all information is relevant, timely, clear and accurate;</li>
        <li>Identify trusted sources and repeat key messages.</li>
      </ul>
    </div>
    <div class="principle">
      <div class="principle__icon"><svg width="11" height="11" viewBox="0 0 12 12"><path d="M6,11 V5 M6,6 C3,6 2,4 2,2 C4.5,2 6,3.5 6,6 M6,5 C6,3 7.5,1.5 10,1.5 C10,3.8 8.5,5 6,5" fill="none" stroke="#5c9b4a" stroke-width="1"/></svg></div>
      <h3 class="principle__title">Recognise and build <strong>capacity</strong>:</h3>
      <ul>
        <li>Assess capability and capacity before, during and after an event;</li>
        <li>Support self-reliance, preparation and mitigation;</li>
        <li>Develop networks and partnerships to strengthen resilience;</li>
        <li>Ensure wellbeing supports are available for staff and volunteers;</li>
        <li>Know when and how to step back as the community is ready.</li>
      </ul>
    </div>
  </div>
</section>

</body>
</html>
```